TA BRAMLEY BUSINESS CARD DESIGN PROJECT

We need to utilize our logo that was expertly created on PixelHarbor and now need to match this with a business card design.

```html
<!DOCTYPE html>
<html lang="en">
<head>
<meta charset="utf-8">
<title>TA BRAMLEY – Business Card</title>
<link href="https://fonts.googleapis.com/css2?family=Montserrat:wght@400;700&display=swap" rel="stylesheet">
<style>
  :root {
    --backdrop: #4a4a4a;
    --card: #161616;
    --brand-blue: #0f56ab;
    --text-light: #f2f2f2;
    --mark-grey: #2c2c2c;
  }
  * { box-sizing: border-box; margin: 0; padding: 0; }
  html, body { width: 1200px; height: 801px; overflow: hidden; }
  body {
    background: var(--backdrop);
    font-family: "Montserrat", Arial, sans-serif;
    display: flex;
    align-items: center;
    justify-content: center;
    gap: 40px;
  }
  .card {
    position: relative;
    width: 540px;
    height: 309px;
    background: var(--card);
    overflow: hidden;
    box-shadow: 0 14px 30px rgba(0,0,0,.35);
  }
  .card-front .brand-name {
    position: absolute;
    left: 40px;
    top: 128px;
    color: var(--brand-blue);
    font-weight: 700;
    font-size: 30px;
    letter-spacing: 2px;
  }
  .divider {
    position: absolute;
    left: 268px;
    top: 78px;
    width: 1.5px;
    height: 150px;
    background: var(--brand-blue);
  }
  .contact {
    position: absolute;
    left: 292px;
    top: 44px;
    color: var(--text-light);
    font-size: 12.5px;
    line-height: 1.35;
  }
  .contact .person-name {
    color: var(--brand-blue);
    font-weight: 700;
    font-size: 17px;
    letter-spacing: .5px;
    line-height: 1.2;
  }
  .contact .role { margin-bottom: 12px; }
  .contact-list { list-style: none; margin-bottom: 12px; }
  .contact-list li { display: flex; align-items: center; gap: 7px; }
  .contact-list svg { width: 10px; height: 10px; fill: var(--brand-blue); flex: none; }
  .edge-band { position: absolute; left: 0; bottom: 0; }
  .card-back {
    display: flex;
    align-items: center;
    justify-content: center;
  }
  .card-back .brand-name {
    color: var(--mark-grey);
    font-weight: 700;
    font-size: 52px;
    letter-spacing: 5px;
  }
</style>
</head>
<body>
  <section class="card card-front">
    <div class="brand-name">TA BRAMLEY</div>
    <div class="divider"></div>
    <div class="contact">
      <div class="person-name">MARTIN COLE</div>
      <div class="role">Managing Director</div>
      <ul class="contact-list">
        <li><svg viewBox="0 0 10 10"><path d="M2 0.5 L4 2.5 L3 4 Q4.5 6 6 7 L7.5 6 L9.5 8 L8 9.5 Q3 9 0.5 2 Z"/></svg>123 456 789</li>
        <li><svg viewBox="0 0 10 10"><rect x="2.5" y="0.5" width="5" height="9" rx="1"/></svg>123 456 789</li>
        <li><svg viewBox="0 0 10 10"><path d="M0.5 2 H9.5 V8.5 H0.5 Z M0.5 2 L5 5.5 L9.5 2" stroke="#161616" stroke-width="0.8"/></svg>info@tabramley.com</li>
        <li><svg viewBox="0 0 10 10"><circle cx="5" cy="5" r="4.5"/></svg>www.tabramley.com</li>
      </ul>
      <div class="address">Your address, City<br>State, Zip 1234</div>
    </div>
    <svg class="edge-band" width="540" height="40" viewBox="0 0 540 40">
      <polygon points="300,18 540,18 540,40 296,40" fill="var(--brand-blue)"/>
      <polygon points="0,26 292,22 292,25 0,29" fill="var(--brand-blue)"/>
      <polygon points="0,32 294,30 294,34 0,36" fill="var(--brand-blue)"/>
    </svg>
  </section>

  <section class="card card-back">
    <div class="brand-name">TA BRAMLEY</div>
  </section>
</body>
</html>
```